Tree Service Billboard 20x8 ft

We need a billboard design for a tree service company.
The billboard is 20ft x 8 ft so we need a design that is capable to stretching to those dimensions without loosing quality.
I have attached a series of images.
Image 1- Simply a billboard that I think looks good that I would like you to use for inspiration. I am aiming for the same format only no color in the wording, just black white, or gray. I like the the trees in the background, the logo placed to the left, and wording on the right.
Image 2- Current Logo I would like to the left of the billboard
Image 3- Another format of current logo if needed.
Image 4- A drawn out design template
Image 5- Another drawn out design template

Specific things I am looking for
-The contact number to be the largest thing on the design
-The logo on the design
-Key points to the design to say:
Tree Removal
Tree Trimming
Land Development
Stump Grinding
Storm Response
Insured
Free Bids
-The facebook logo
-The Google Logo

```html
<!DOCTYPE html>
<html lang="en">
<head>
<meta charset="utf-8">
<title>Tree Service Billboard 20x8 ft</title>
<link href="https://fonts.googleapis.com/css2?family=Anton&family=Montserrat:wght@500;700&display=swap" rel="stylesheet">
<style>
  :root {
    --page: #f1f1f1;
    --ink: #000000;
    --paper: #ffffff;
    --steel: #666666;
    --forest-dark: #1d2a14;
    --forest-mid: #3f5a25;
    --forest-light: #9fae6a;
  }
  * { margin: 0; padding: 0; box-sizing: border-box; }
  html, body { width: 1200px; height: 833px; overflow: hidden; background: var(--page); }
  .canvas { position: relative; width: 1200px; height: 833px; }

  .board-title {
    position: absolute; left: 0; right: 0; top: 155px;
    text-align: center;
    font-family: "Montserrat", sans-serif; font-weight: 500;
    font-size: 44px; letter-spacing: 3px; color: var(--ink);
  }

  .billboard { position: absolute; left: 63px; top: 240px; width: 1074px; height: 429px; }
  .billboard-shapes { position: absolute; inset: 0; }

  .brand-name {
    position: absolute; left: 88px; top: 213px; width: 380px;
    text-align: center;
    font-family: "Anton", sans-serif; font-size: 46px; line-height: 1;
    color: var(--paper); letter-spacing: 0.5px;
  }

  .phone-icon { position: absolute; left: 20px; top: 332px; width: 48px; height: 52px; }
  .phone-number {
    position: absolute; left: 86px; top: 320px;
    font-family: "Anton", sans-serif; font-size: 70px; line-height: 1;
    letter-spacing: 6px; color: var(--paper);
  }

  .social-dot {
    position: absolute; top: 335px; width: 48px; height: 48px;
    border: 3px solid var(--paper); border-radius: 50%;
  }
  .social-dot.first { left: 564px; }
  .social-dot.second { left: 629px; }

  .service-list {
    position: absolute; right: 36px; top: 30px;
    list-style: none; text-align: right;
    font-family: "Anton", sans-serif; font-size: 45px; line-height: 62.5px;
    color: var(--ink);
  }

  .insured-badge { position: absolute; left: 816px; top: 343px; width: 178px; height: 66px; }
</style>
</head>
<body>
<div class="canvas">
  <h1 class="board-title">TREE SERVICE BILLBOARD 20X8 FT</h1>

  <div class="billboard">
    <svg class="billboard-shapes" width="1074" height="429" viewBox="0 0 1074 429">
      <defs>
        <radialGradient id="forestGlow" cx="0.68" cy="0.35" r="0.75">
          <stop offset="0" stop-color="var(--forest-light)"/>
          <stop offset="0.35" stop-color="var(--forest-mid)"/>
          <stop offset="1" stop-color="var(--forest-dark)"/>
        </radialGradient>
        <linearGradient id="emblemFill" x1="0" y1="0" x2="0" y2="1">
          <stop offset="0" stop-color="#2a2a2a"/>
          <stop offset="1" stop-color="#7a7a7a"/>
        </linearGradient>
      </defs>
      <rect class="forest-photo" x="0" y="0" width="860" height="310" fill="url(#forestGlow)" role="img" aria-label="Photo of a sunlit green forest with tall trees"/>
      <rect x="0" y="307" width="822" height="106" fill="var(--ink)"/>
      <polygon points="0,413 822,413 800,413 800,429 0,429" fill="var(--steel)"/>
      <path d="M780,0 C720,80 690,170 693,230 C696,320 740,400 800,429 L0,429 L0,413 L822,413 L822,429 L860,429 Z" fill="var(--steel)"/>
      <path d="M808,0 L1074,0 L1074,429 L800,429 C740,395 694,320 693,230 C694,150 740,50 808,0 Z" fill="var(--steel)"/>
      <path d="M820,0 L1074,0 L1074,429 L805,429 C750,390 705,320 704,230 C705,145 752,55 820,0 Z" fill="var(--paper)"/>
      <circle cx="271" cy="120" r="90" fill="var(--paper)"/>
      <circle cx="271" cy="120" r="82" fill="url(#emblemFill)" role="img" aria-label="Company emblem placeholder"/>
    </svg>

    <div class="brand-name">HARTWELL TREE SERVICE</div>

    <svg class="phone-icon" viewBox="0 0 48 52" aria-hidden="true">
      <path d="M6,6 C2,10 2,18 8,28 C14,38 22,46 32,50 C38,52 42,48 44,44 L36,36 C34,34 31,35 29,37 C24,35 18,28 15,22 C17,20 18,17 16,15 L10,6 C9,4 7,5 6,6 Z" fill="var(--paper)"/>
      <path d="M26,8 A14,14 0 0 1 40,22 M26,16 A6,6 0 0 1 32,22" stroke="var(--paper)" stroke-width="3" fill="none" stroke-linecap="round"/>
    </svg>
    <div class="phone-number">417-555-0148</div>

    <span class="social-dot first" aria-label="Social page"></span>
    <span class="social-dot second" aria-label="Reviews page"></span>

    <ul class="service-list">
      <li>TREE REMOVAL</li>
      <li>TREE TRIMMING</li>
      <li>LAND DEVELOPMENT</li>
      <li>STUMP GRINDING</li>
      <li>STORM RESPONSE</li>
    </ul>

    <svg class="insured-badge" viewBox="0 0 178 66">
      <rect x="50" y="7" width="126" height="49" rx="24.5" fill="var(--ink)" stroke="var(--paper)" stroke-width="2"/>
      <path d="M2,6 L28,0 L56,6 L56,34 C56,50 42,60 28,66 C14,60 2,50 2,34 Z" fill="var(--ink)"/>
      <path d="M14,32 L25,44 L45,14" stroke="var(--paper)" stroke-width="6" fill="none" stroke-linecap="round" stroke-linejoin="round"/>
      <text x="113" y="39" text-anchor="middle" font-family="Montserrat, sans-serif" font-weight="700" font-size="20" fill="var(--paper)">INSURED</text>
    </svg>
  </div>
</div>
</body>
</html>
```